R7M Horizon Business Card Design

We need a business card created for our New Business "R7M Horizon"<br/><br/>The business card design is up to you however the following information must be on the business card:<br/><br/>Front of the business card -<br/>Email :darrenp@r7mhorizon.nz<br/>Mobile: +64 (0) 22 4870 619<br/>Website: www.r7mhorizon.nz<br/>Card Owner Name: Darren Paltrow<br/>Company Title: Business Development Manager<br/>Slogan: "The PEAK of every horizon". <br/>Logo On the front attached to the design brief<br/><br/>On the back: <br/>Space on the back for 4 more versions of the logo across the bottom of the card indicating different subsidiary brands - R7M Coffee, R7M Arts, R7M ?? (The card will be used for all of these brands - We Will add the extra subsidiary logos to the design once the design is finished (We are a graphics design team). <br/><br/>Other than that we want a premium feeling logo that remains universally usable depending on the business entity that we are using the card for. The use of bright bold colours would be great but we still want the card to feel premium.
Target Market(s)
Gift Design and Manufacturing Companies
Contact Information for Business Card
Front of the business card -
Email :darrenp@r7mhorizon.nz
Mobile: +64 (0) 22 4870 619
Website: www.r7mhorizon.nz
Card Owner Name: Darren Paltrow
Company Title: Business Development Manager
Slogan: "The PEAK of every horizon".
Logo On the front attached to the design brief

```html
<!DOCTYPE html>
<html lang="en">
<head>
<meta charset="utf-8">
<title>R7M Horizon Business Card</title>
<link rel="stylesheet" href="https://fonts.googleapis.com/css2?family=Exo+2:wght@400;700&family=Open+Sans:wght@400&family=Syncopate:wght@700&display=swap">
<style>
  :root {
    --brand-blue: #3545a0;
    --brand-blue-light: #4654ab;
    --ink: #333338;
    --paper: #ffffff;
    --backdrop: #2a2a2c;
  }
  * { box-sizing: border-box; margin: 0; padding: 0; }
  html, body { width: 1200px; height: 900px; overflow: hidden; }
  body { background: var(--backdrop); position: relative; font-family: "Open Sans", sans-serif; }

  .card {
    position: absolute;
    left: 250px;
    width: 700px;
    height: 400px;
    border-radius: 18px;
    overflow: hidden;
  }

  /* Back of card */
  .card-back {
    top: 45px;
    background: linear-gradient(100deg, var(--brand-blue) 0%, var(--brand-blue-light) 100%);
    color: var(--paper);
  }
  .back-wordmark {
    position: absolute;
    top: 130px;
    left: 0; right: 0;
    display: flex;
    align-items: center;
    justify-content: center;
    gap: 18px;
    font-family: "Exo 2", sans-serif;
    font-weight: 700;
    font-size: 58px;
    letter-spacing: 1px;
  }
  .back-wordmark .mark-dot {
    width: 26px; height: 26px; border-radius: 50%; background: var(--paper);
  }
  .back-tagline {
    position: absolute;
    top: 325px;
    left: 0; right: 0;
    display: flex;
    align-items: center;
    justify-content: center;
    gap: 12px;
    font-family: "Exo 2", sans-serif;
    font-size: 19px;
    letter-spacing: 0.5px;
  }
  .back-tagline strong { font-weight: 700; }

  /* Front of card */
  .card-front {
    top: 475px;
    background: var(--paper);
  }
  .name-rule {
    position: absolute;
    left: 30px; top: 24px;
    width: 2px; height: 64px;
    background: var(--brand-blue);
  }
  .holder-name {
    position: absolute;
    left: 48px; top: 22px;
    font-family: "Syncopate", sans-serif;
    font-weight: 700;
    font-size: 28px;
    line-height: 36px;
    color: var(--brand-blue);
    letter-spacing: 1px;
  }
  .holder-title {
    position: absolute;
    left: 48px; top: 64px;
    font-size: 18px;
    line-height: 24px;
    color: var(--ink);
    letter-spacing: 0.5px;
  }
  .logo-band {
    position: absolute;
    top: 140px; left: 620px; right: 0;
    height: 62px;
    background: var(--brand-blue);
  }
  .front-wordmark {
    position: absolute;
    top: 150px; right: 90px;
    height: 42px;
    display: flex;
    align-items: center;
    gap: 10px;
    font-family: "Exo 2", sans-serif;
    font-weight: 700;
    font-size: 30px;
    color: var(--brand-blue);
  }
  .front-wordmark .mark-dot {
    width: 14px; height: 14px; border-radius: 50%; background: var(--brand-blue);
  }
  .contact-band {
    position: absolute;
    left: 0; right: 0; top: 258px;
    height: 108px;
    background: var(--brand-blue);
    color: var(--paper);
  }
  .contact-list {
    position: absolute;
    left: 50px; top: 12px;
    list-style: none;
    font-size: 19px;
    line-height: 28px;
  }
  .contact-list li { display: flex; align-items: center; gap: 10px; }
  .contact-list svg { width: 15px; height: 15px; flex: none; }
  .slogan-pill {
    position: absolute;
    right: 36px; top: 34px;
    padding: 5px 24px;
    border: 2px solid var(--paper);
    border-radius: 28px;
    font-family: "Exo 2", sans-serif;
    font-size: 23px;
    line-height: 30px;
    letter-spacing: 0.3px;
    white-space: nowrap;
  }
  .slogan-pill strong { font-weight: 700; }
</style>
</head>
<body>

<section class="card card-back" aria-label="Card back">
  <div class="back-wordmark"><span>R7M Horizon</span><span class="mark-dot"></span></div>
  <p class="back-tagline">
    <svg width="12" height="10" viewBox="0 0 12 10" aria-hidden="true"><polygon points="0,5 12,0 12,10" fill="#fff"/></svg>
    <span>The <strong>PEAK</strong> of every horizon</span>
    <svg width="12" height="10" viewBox="0 0 12 10" aria-hidden="true"><polygon points="12,5 0,0 0,10" fill="#fff"/></svg>
  </p>
</section>

<section class="card card-front" aria-label="Card front">
  <span class="name-rule"></span>
  <h1 class="holder-name">DARREN PALTROW</h1>
  <p class="holder-title">Business Development Manager</p>

  <div class="logo-band"></div>
  <div class="front-wordmark"><span>R7M Horizon</span><span class="mark-dot"></span></div>

  <div class="contact-band">
    <ul class="contact-list">
      <li>
        <svg viewBox="0 0 16 16" aria-hidden="true"><path d="M4 1l2.5 3-1.5 1.5c.8 2 2.5 3.7 4.5 4.5L11 8.5l3 2.5-1.5 3C7 14 2 9 2 3z" fill="none" stroke="#fff" stroke-width="1.4" stroke-linejoin="round"/></svg>
        <span>+64 (0) 22 4870 619</span>
      </li>
      <li>
        <svg viewBox="0 0 16 16" aria-hidden="true"><rect x="1" y="3" width="14" height="10" fill="none" stroke="#fff" stroke-width="1.4"/><path d="M1 3l7 6 7-6" fill="none" stroke="#fff" stroke-width="1.4"/></svg>
        <span>darrenp@r7mhorizon.nz</span>
      </li>
      <li>
        <svg viewBox="0 0 16 16" aria-hidden="true"><circle cx="8" cy="8" r="6.5" fill="none" stroke="#fff" stroke-width="1.3"/><ellipse cx="8" cy="8" rx="3" ry="6.5" fill="none" stroke="#fff" stroke-width="1.1"/><path d="M1.5 8h13M2.5 5h11M2.5 11h11" stroke="#fff" stroke-width="1"/></svg>
        <span>www.r7mhorizon.nz</span>
      </li>
    </ul>
    <p class="slogan-pill">The <strong>PEAK</strong> of every horizon</p>
  </div>
</section>

</body>
</html>
```